Book Title: “Faith: Road of Endless Grace” Please see the attachment “Text on the cover”.

Book Cover Design Instructions: This book is meant for people of all religions and nationalities. Therefore, on the cover, there should be no mosque or an object specific to any religion. The primary emphasis should be on the "unconditional love of God." Therefore, use universal symbols of love. The second priority themes could be Sufism, Peace, and self-improvement. Rest is your imagination. Please also see the attachment: 'Book description and author's Bio.'
This book has the potential to be a best seller. Please do a good job.
What Book Cover Formats are required: A designer should submit cover designs in three formats: (1) eBook, (2) Paperback, and (3) Hardback. These books will be published on Borvex QPL.
Format requirements for eBooks are available from: https://qpl.borvex.example/en_US/help/topic/R731928457.
You can find paperback and hardback cover measurements from: https://qpl.borvex.example/en_US/cover-calculator
• To complete the project, all three formats should be accepted by Borvex QPL.
• The book interior trim size is 6.14 X 9.21 inches.
• Interior Type: Premium color.
• No bleed.
• I do not upload barcode. So, the back cover should have room for Borvex to print the barcode.
• Number of pages 126.
Compensation for the designer: After selecting one designer, I will increase the amount by $200 on Artvelle to compensate for three deliverables.
Follow-up of the Project:
After the book is published, I may need minor revisions. For example, the number of pages may change. Therefore, I will need the same design in revised sizes. In that case, I will pay $25 for each revision. For example, if the number of pages changes, I will need a different spine for paperback and hardback, then I will pay the artist $25 + $25 = $50 for both designs.
List of Enclosers:
1. Text on the cover.
2. Book description and author's Bio for the back cover.
3. Later, I will upload my picture for the book's back cover.

Target Market(s)

Any adult

Industry/Entity Type

Any industry

Requirements
Must have
• Three Deliverables

```html
<!DOCTYPE html>
<html lang="en">
<head>
<meta charset="utf-8">
<title>Faith: Road of Endless Grace — Cover Spread</title>
<link rel="stylesheet" href="https://fonts.googleapis.com/css2?family=Cinzel:wght@400;600;700&family=Cormorant+Garamond:ital,wght@1,600&family=Montserrat:wght@400&display=swap">
<style>
  :root {
    --page: #ffffff;
    --back-bg: #131523;
    --ink-light: #ffffff;
    --title-navy: #141a4c;
    --sky-top: #1c2a4e;
    --glow-gold: #ffd35a;
    --cloud-amber: #e9a046;
    --dusk-purple: #4b3550;
    --barcode-space: #ffffff;
  }
  html, body {
    margin: 0;
    width: 1200px;
    height: 1200px;
    overflow: hidden;
    background: var(--page);
  }
  .spread {
    position: absolute;
    left: 50px;
    top: 205px;
    width: 1100px;
    height: 790px;
    display: flex;
  }
  .back-cover {
    position: relative;
    width: 530px;
    background: var(--back-bg);
    color: var(--ink-light);
  }
  .spine {
    position: relative;
    width: 40px;
    background: var(--back-bg);
    color: var(--ink-light);
  }
  .front-cover {
    position: relative;
    width: 530px;
    overflow: hidden;
  }

  /* Back cover */
  .back-title {
    position: absolute;
    left: 33px;
    top: 32px;
    width: 464px;
    margin: 0;
    font: 400 27px/1 "Cinzel", serif;
    letter-spacing: 1.2px;
    white-space: nowrap;
  }
  .back-subtitle {
    position: absolute;
    left: 33px;
    top: 80px;
    width: 464px;
    margin: 0;
    font: 400 14px/1 "Cinzel", serif;
    letter-spacing: 0.6px;
    white-space: nowrap;
  }
  .description {
    position: absolute;
    left: 33px;
    top: 102px;
    width: 462px;
    font: 400 10.6px/12.7px "Montserrat", sans-serif;
    text-align: justify;
  }
  .description p { margin: 0 0 12.7px; }
  .author-photo {
    position: absolute;
    left: 33px;
    top: 548px;
    width: 133px;
    height: 169px;
    background: var(--barcode-space);
  }
  .author-name-back {
    position: absolute;
    left: 183px;
    top: 549px;
    margin: 0;
    font: 400 16px/1 "Cinzel", serif;
    letter-spacing: 0.6px;
  }
  .author-bio {
    position: absolute;
    left: 183px;
    top: 571px;
    width: 312px;
    margin: 0;
    font: 400 10.6px/12.7px "Montserrat", sans-serif;
    text-align: justify;
  }
  .barcode-area {
    position: absolute;
    left: 306px;
    top: 657px;
    width: 190px;
    height: 102px;
    background: var(--barcode-space);
  }

  /* Spine */
  .spine-text {
    position: absolute;
    left: 8px;
    top: 0;
    width: 790px;
    height: 24px;
    transform-origin: 0 0;
    transform: translate(30px, 0) rotate(90deg);
    font: 400 22px/24px "Cinzel", serif;
    white-space: nowrap;
  }
  .spine-title { position: absolute; left: 40px; letter-spacing: 1px; }
  .spine-author { position: absolute; left: 534px; letter-spacing: 1px; }

  /* Front cover */
  .cover-art {
    position: absolute;
    inset: 0;
    background:
      radial-gradient(ellipse 150px 170px at 262px 230px, rgba(255,246,200,0.95), rgba(255,211,90,0.75) 45%, rgba(255,180,60,0) 100%),
      radial-gradient(ellipse 340px 260px at 262px 420px, rgba(233,160,70,0.9), rgba(233,160,70,0) 100%),
      linear-gradient(180deg, var(--sky-top) 0%, #2f4670 22%, #c88a4c 48%, var(--cloud-amber) 62%, #8b6070 82%, var(--dusk-purple) 100%);
  }
  .front-title {
    position: absolute;
    left: 0;
    width: 530px;
    margin: 0;
    text-align: center;
    color: var(--title-navy);
    font-family: "Cinzel", serif;
    font-weight: 700;
    line-height: 1;
  }
  .front-title span { display: block; }
  .title-line-1 { font-size: 104px; margin-top: 388px; letter-spacing: 2px; }
  .title-line-2 { font-size: 72px; margin-top: -6px; }
  .title-line-3 { font-size: 55px; margin-top: -2px; letter-spacing: 0.5px; }
  .front-subtitle {
    position: absolute;
    left: 0;
    top: 624px;
    width: 530px;
    margin: 0;
    text-align: center;
    color: var(--ink-light);
    font: italic 600 29px/32px "Cormorant Garamond", serif;
    font-variant: small-caps;
    letter-spacing: 1.2px;
  }
  .front-author {
    position: absolute;
    left: 0;
    top: 722px;
    width: 530px;
    margin: 0;
    text-align: center;
    color: var(--ink-light);
    font: 600 32px/1 "Cinzel", serif;
    letter-spacing: 1.5px;
  }
</style>
</head>
<body>
  <main class="spread">
    <section class="back-cover">
      <h2 class="back-title">FAITH: ROAD OF ENDLESS GRACE</h2>
      <h3 class="back-subtitle">GUIDE TO CULTIVATING INNER PEACE AND MINDFUL LIVING</h3>
      <div class="description">
        <p>This book intricately intertwines the diverse teachings of Sufism with the deep wisdom of the Quran to create a comprehensive roadmap for personal spiritual growth. The reader has a chance to experience firsthand the profound peace and boundless love Sufis have cherished for centuries. This book addresses the following critical questions:</p>
        <p>How can one unconditionally love God? It is the greatest of all kinds of love that ignites a profound and transformative spiritual journey.</p>
        <p>How to feel the love of God, which can bring immense peace and contentment.</p>
        <p>How to unconditionally love yourself, which nurtures personal growth and harmony.</p>
        <p>What is the most effective way to respond to life’s critical crises to reduce suffering and expedite recovery?</p>
        <p>This book also explores Islam’s overwhelming emphasis on avoiding Zulm (oppression and injustice) because the Quran mentions the word Zulm an astounding 291 times. Avoiding Zulm in all human interactions should be the top priority for every Muslim.</p>
        <p>Prophet Muhammad (PBUH) did not just preach peace and love. He gave us a practical example when he took over as a ruler of the Medina without bloodshed. He did not inherit power through the dynasty, and Medina was multi-religious. Arguably, it was history’s first large-scale peaceful transfer of power.</p>
        <p>Similarly, he signed the Treaty of Hudaybia with the staunchest enemy, employing an unprecedented peaceful strategy to nonviolently end a bitter war that had claimed hundreds of lives.</p>
        <p>The highlight of this book is that it points to the methodology to acquire a fully satisfied and contented soul (Nafs-e-Mutma’inna) in practical steps, which is the goal of every Sufi wayfarer.</p>
      </div>
      <div class="author-photo" role="img" aria-label="Space for the author's portrait"></div>
      <h3 class="author-name-back">DR. IDRIS HALVANI</h3>
      <p class="author-bio">Dr. Halvani holds a Master’s in Physics and a Master’s in Computer Science and worked as a Software Engineer. He earned his Ph.D. in Islamic Studies. He was one of the founders of a mosque in Virginia.</p>
      <div class="barcode-area" aria-label="Reserved space for barcode"></div>
    </section>

    <section class="spine">
      <div class="spine-text">
        <span class="spine-title">FAITH: ROAD OF ENDLESS GRACE</span>
        <span class="spine-author">DR. IDRIS HALVANI</span>
      </div>
    </section>

    <section class="front-cover">
      <div class="cover-art" role="img" aria-label="Illustration of a glowing golden heart radiating light above a sea of warm clouds under a starry night sky"></div>
      <h1 class="front-title">
        <span class="title-line-1">FAITH</span>
        <span class="title-line-2">ROAD OF</span>
        <span class="title-line-3">ENDLESS GRACE</span>
      </h1>
      <p class="front-subtitle">Guide to Cultivating Inner<br>Peace and Mindful Living</p>
      <p class="front-author">DR. IDRIS HALVANI</p>
    </section>
  </main>
</body>
</html>
```